New Innovative Counselling and psychotherapy Service needs Business Card design

Keep it simple and professional. On one side, just company name and logo (perhaps in all blue) and maybe a tag line.

On other side (all white) my name and Qualifications in centre

Industry/Entity Type

Health And Wellness

Contact Information for Business Card

Dara Whelby
Counsellor & Psychotherapist
BSc (Psychol.), BA, Dip. (Couns. & Psych.), PG.Cert (CBT), FGTrK, ONRE

I will also require Mobile no, Email and web site address of which I'll pass on to final designer.

Font styles to use
Sans Serif

Requirements
Must have
• My Logo Only and please use the colours in logo that is in it.
Should not have
• Any other images

```html
<!DOCTYPE html>
<html lang="en">
<head>
<meta charset="utf-8">
<title>Steady Harbour – Business Card</title>
<link href="https://fonts.googleapis.com/css2?family=Roboto:wght@400;500;700&display=swap" rel="stylesheet">
<style>
  :root {
    --sky: #4fb6ea;
    --sky-deep: #3fa3dc;
    --leaf: #86c350;
    --leaf-deep: #6fb33a;
    --paper: #ffffff;
    --paper-shade: #f3f4f4;
    --ink: #333333;
    --backdrop: #e4e5e6;
  }
  * { margin: 0; padding: 0; box-sizing: border-box; }
  html, body { width: 1200px; height: 726px; overflow: hidden; }
  body {
    background: var(--backdrop);
    font-family: "Roboto", Arial, sans-serif;
    position: relative;
  }
  .card {
    position: absolute;
    top: 214px;
    width: 520px;
    height: 298px;
    overflow: hidden;
    box-shadow: 0 6px 18px rgba(0,0,0,0.12);
  }
  /* Front */
  .card-front {
    left: 40px;
    background: var(--sky);
    display: flex;
    align-items: center;
    justify-content: center;
  }
  .brand-lockup { display: flex; align-items: center; gap: 16px; }
  .brand-dot {
    width: 54px; height: 54px; border-radius: 50%;
    background: var(--paper);
    flex: none;
  }
  .brand-text { color: var(--paper); }
  .brand-name {
    font-size: 40px; font-weight: 400; letter-spacing: 0.5px; line-height: 1;
  }
  .brand-tagline {
    margin-top: 8px;
    font-size: 13px; letter-spacing: 6.5px;
  }
  /* Back */
  .card-back {
    left: 640px;
    background: linear-gradient(180deg, var(--paper), var(--paper-shade));
  }
  .card-back .wave { position: absolute; inset: 0; }
  .holder {
    position: absolute; top: 16px; right: 20px;
    text-align: right; color: var(--paper);
  }
  .holder-name { font-size: 20px; font-weight: 700; line-height: 1.2; margin-bottom: 3px; }
  .holder-role, .holder-quals { font-size: 10.5px; line-height: 1.35; }
  .contact {
    position: absolute; top: 150px; right: 20px;
    list-style: none; text-align: right; color: var(--ink);
    font-size: 13px; line-height: 1.55;
  }
  .contact li { display: flex; justify-content: flex-end; align-items: center; gap: 7px; }
  .contact svg { width: 11px; height: 11px; flex: none; }
  .back-brand {
    position: absolute; left: 26px; bottom: 20px;
    display: flex; flex-direction: column; align-items: flex-start; gap: 10px;
  }
  .back-brand .brand-dot { width: 76px; height: 76px; margin-left: 120px; background: var(--sky-deep); }
  .back-brand .brand-name { color: var(--ink); font-size: 28px; }
</style>
</head>
<body>

<section class="card card-front" aria-label="Card front">
  <div class="brand-lockup">
    <span class="brand-dot"></span>
    <div class="brand-text">
      <p class="brand-name">Steady Harbour</p>
      <p class="brand-tagline">A tag line goes here</p>
    </div>
  </div>
</section>

<section class="card card-back" aria-label="Card back">
  <svg class="wave" viewBox="0 0 520 298" preserveAspectRatio="none" aria-hidden="true">
    <path d="M0 0 H520 V118 C400 118 200 124 0 150 Z" fill="var(--sky)"/>
    <path d="M0 150 C200 124 400 118 520 118 V126 C400 126 200 132 0 160 Z" fill="var(--leaf)"/>
    <path d="M0 166 C170 140 330 132 470 130 C330 140 170 152 0 178 Z" fill="var(--leaf-deep)"/>
  </svg>

  <div class="holder">
    <p class="holder-name">Dara Whelby</p>
    <p class="holder-role">Counsellor &amp; Psychotherapist</p>
    <p class="holder-quals">BSc (Psychol.), BA, Dip. (Couns.<br>&amp; Psych.), PG.Cert (CBT),<br>FGTrK, ONRE</p>
  </div>

  <ul class="contact">
    <li>0123 456 7890
      <svg viewBox="0 0 12 12" aria-hidden="true"><path d="M3 1 L5 3.5 L4 5 C4.6 6.4 5.6 7.4 7 8 L8.5 7 L11 9 L9.6 11 C5 10.6 1.4 7 1 2.4 Z" fill="var(--sky-deep)"/></svg>
    </li>
    <li>dara.w@SteadyHarbour.com
      <svg viewBox="0 0 12 12" aria-hidden="true"><rect x="1" y="2.5" width="10" height="7" fill="var(--leaf-deep)"/><path d="M1 2.5 L6 6.5 L11 2.5" stroke="#fff" fill="none"/></svg>
    </li>
    <li>www.SteadyHarbour.com
      <svg viewBox="0 0 12 12" aria-hidden="true"><circle cx="6" cy="6" r="5" fill="var(--sky-deep)"/><path d="M1 6 H11 M6 1 C3.5 4 3.5 8 6 11 M6 1 C8.5 4 8.5 8 6 11" stroke="#fff" stroke-width="0.7" fill="none"/></svg>
    </li>
  </ul>

  <div class="back-brand">
    <span class="brand-dot"></span>
    <p class="brand-name">Steady Harbour</p>
  </div>
</section>

</body>
</html>
```